accomplished personal trainer, former elite gymnast from Russia, highly professional and experienced

Established Fitness trainer in California requires a new web site to attract personal clients and build her group exercise classes.

Here is an example of another fitness trainer's site that I really liked the technology:
http://www.tedvorlam.com

Below I have inserted my current web site: www.quelbornfitnesslodi.com
You can use this web site for the principal content, such as my background and qualifications.

Target Market(s)

Anyone who wants to improve their fitness levels and wellness in general. Anyone who needs directions and instruction on how to exercise. I can train anyone from elite athlete to a disabled person.

Industry/Entity Type

Fitness

Coding

Coded - Design and coding required

Number of Pages Required

5+ page

Font styles to use
Sans Serif

Requirements
Must have
• Easy to navigate main info about me, location, services, contact, benefits of using my services.
• Would be great to create unique representation of me as a trainer and a person, using new technologies and new ideas. Make it different from the other websites. Having its own character. Not too complicated and heavy with information, but an eye catching, useful and fun to navigate.
Nice to have
• new technology, easy access to information, the idea of enjoyment of life, lightness about achieving any goal, spiritual wisdom, unique design. I am planning to insert educational videos, advise, maybe jokes. Sign in, shopping cart, logo, should be easy for me to make changes in content.
Should not have
• cliché, outdated technology, too complicated,

```html
<!DOCTYPE html>
<html lang="en">
<head>
<meta charset="utf-8">
<title>Quelborn Fitness Lodi</title>
<link rel="stylesheet" href="https://fonts.googleapis.com/css2?family=Roboto:wght@300;400;500;700&family=Tinos:ital@1&display=swap">
<style>
  :root {
    --ink: #000000;
    --charcoal: #1b1b1b;
    --header: #1a1a1a;
    --bottom-bar: #3a3a3a;
    --white: #ffffff;
    --soft-text: #e6e6e6;
    --field-line: #e2e2e2;
    --placeholder: #c8c8c8;
    --dark-text: #222222;
  }
  * { box-sizing: border-box; margin: 0; padding: 0; }
  html, body { width: 1200px; height: 2936px; overflow: hidden; background: var(--white); }
  body { font-family: "Roboto", Arial, sans-serif; color: var(--white); }
  .page { position: relative; width: 1200px; height: 2936px; overflow: hidden; }
  .line { display: block; white-space: nowrap; }

  .site-header { position: absolute; top: 0; left: 0; width: 1200px; height: 110px; background: var(--header); display: flex; align-items: center; justify-content: center; }
  .site-title { font-weight: 700; font-size: 33px; letter-spacing: 0.3px; }

  .main-nav { position: absolute; top: 110px; left: 0; width: 1200px; height: 50px; background: var(--ink); }
  .nav-item { position: absolute; top: 0; height: 50px; line-height: 50px; font-size: 15px; transform: translateX(-50%); white-space: nowrap; }
  .nav-item.is-active { top: 7px; height: 38px; line-height: 36px; width: 180px; text-align: center; border: 2px solid #cfcfcf; }

  .photo { position: absolute; left: 0; width: 1200px; }
  .hero-photo { top: 160px; height: 458px; background: linear-gradient(180deg, #6f8a4a 0%, #8fa35f 35%, #4f6a3a 62%, #7fa04c 100%); }
  .hero-shade { position: absolute; inset: 0; background: rgba(0,0,0,0.12); }
  .hero-title { position: absolute; top: 318px; left: 0; width: 1200px; text-align: center; font-weight: 300; font-size: 60px; }
  .outline-button { position: absolute; border: 2px solid var(--white); text-align: center; color: var(--white); font-size: 20px; text-transform: uppercase; white-space: nowrap; }
  .hero-contact { left: 505px; top: 407px; width: 188px; height: 43px; line-height: 39px; font-size: 22px; }

  .testimonial { position: absolute; top: 618px; left: 0; width: 1200px; height: 253px; background: var(--charcoal); }
  .quote-text { position: absolute; top: 42px; left: 150px; width: 900px; text-align: center; font-family: "Tinos", "Times New Roman", serif; font-style: italic; font-size: 18px; line-height: 26px; color: var(--soft-text); }
  .quote-mark { position: absolute; font-family: "Tinos", "Times New Roman", serif; font-weight: 700; font-size: 48px; line-height: 1; }
  .quote-open { left: 112px; top: 46px; }
  .quote-close { left: 1060px; top: 174px; }
  .quote-author { left: 474px; top: 165px; width: 252px; height: 41px; line-height: 37px; }

  .content-band { position: absolute; left: 0; width: 1200px; background: var(--ink); }
  .group-band { top: 871px; height: 378px; }
  .training-band { top: 1632px; height: 378px; }
  .section-heading { position: absolute; font-weight: 400; font-size: 32px; white-space: nowrap; }
  .section-copy { position: absolute; font-size: 14.5px; line-height: 22px; color: var(--soft-text); }
  .group-band .section-heading { left: 114px; top: 46px; }
  .group-band .section-copy { left: 114px; top: 106px; }
  .solid-button { position: absolute; left: 114px; top: 272px; width: 125px; height: 33px; line-height: 33px; background: var(--white); color: var(--ink); font-size: 16px; text-align: center; }
  .inset-photo { position: absolute; }
  .group-photo { left: 646px; top: 59px; width: 438px; height: 264px; background: linear-gradient(160deg, #3e5a2c 0%, #5f7f3c 45%, #88a85a 75%, #6d8a45 100%); }
  .training-photo { left: 114px; top: 59px; width: 440px; height: 264px; background: linear-gradient(200deg, #2f4a24 0%, #557a35 50%, #7e9c55 100%); }
  .training-band .section-heading { right: 114px; top: 46px; text-align: right; }
  .training-band .section-copy { right: 114px; top: 120px; text-align: right; }
  .training-more { left: 959px; top: 292px; width: 127px; height: 31px; line-height: 27px; font-size: 16px; }

  .stretch-photo { top: 1249px; height: 383px; background: linear-gradient(180deg, #3c5530 0%, #50693a 45%, #6f8f46 78%, #5d8a3a 100%); }
  .group-stretch-photo { top: 2010px; height: 382px; background: linear-gradient(180deg, #5b7a3c 0%, #7d9c50 40%, #6a7a58 75%, #4a5a3a 100%); }

  .subscribe { position: absolute; top: 2392px; left: 0; width: 1200px; height: 305px; background: var(--white); color: var(--dark-text); text-align: center; }
  .subscribe-title { position: absolute; top: 24px; left: 0; width: 1200px; font-weight: 400; font-size: 28px; }
  .subscribe-note { position: absolute; top: 75px; left: 0; width: 1200px; font-size: 14px; }
  .field { position: absolute; top: 121px; width: 233px; height: 47px; border: 1px solid var(--field-line); text-align: left; padding-left: 14px; line-height: 45px; font-size: 12px; color: var(--placeholder); }
  .signup-button { position: absolute; left: 550px; top: 191px; width: 123px; height: 45px; line-height: 43px; border: 1.5px solid var(--dark-text); font-size: 14px; }
  .privacy-note { position: absolute; top: 260px; left: 0; width: 1200px; font-size: 11px; }

  .contact-footer { position: absolute; top: 2697px; left: 0; width: 1200px; height: 184px; background: var(--charcoal); }
  .contact-intro { position: absolute; top: 0; left: 0; width: 616px; height: 184px; background: var(--ink); }
  .contact-notch { position: absolute; left: 616px; top: 72px; }
  .footer-heading { position: absolute; font-weight: 400; font-size: 25px; white-space: nowrap; }
  .contact-intro .footer-heading { left: 114px; top: 32px; }
  .contact-intro p { position: absolute; left: 114px; top: 74px; font-size: 13px; line-height: 17px; color: var(--soft-text); }
  .trainer-card .footer-heading { left: 673px; top: 32px; font-size: 26px; }
  .contact-line { position: absolute; left: 673px; display: flex; align-items: center; gap: 14px; font-size: 14px; }
  .contact-line svg { width: 18px; height: 14px; }

  .bottom-bar { position: absolute; top: 2881px; left: 0; width: 1200px; height: 55px; background: var(--bottom-bar); font-size: 12px; }
  .follow-label { position: absolute; left: 114px; top: 0; line-height: 55px; }
  .social-list { position: absolute; left: 190px; top: 19px; display: flex; gap: 6px; }
  .social-square { width: 17px; height: 17px; background: var(--white); border-radius: 2px; }
  .copyright { position: absolute; right: 114px; top: 0; line-height: 55px; white-space: nowrap; }
</style>
</head>
<body>
<div class="page">

  <header class="site-header">
    <h1 class="site-title">Quelborn Fitness Lodi</h1>
  </header>

  <nav class="main-nav">
    <span class="nav-item is-active" style="left:211px">Group Classes</span>
    <span class="nav-item" style="left:403px">Personal Training</span>
    <span class="nav-item" style="left:599px">About Quelborn</span>
    <span class="nav-item" style="left:793px">Contact</span>
    <span class="nav-item" style="left:988px">Blog</span>
  </nav>

  <section class="photo hero-photo" role="img" aria-label="Group of people doing squats together outdoors in a sunny park">
    <div class="hero-shade"></div>
  </section>
  <h2 class="hero-title">Fitness Outdoors</h2>
  <span class="outline-button hero-contact">Contact</span>

  <section class="testimonial">
    <span class="quote-mark quote-open">&ldquo;</span>
    <p class="quote-text">
      <span class="line">I have known Mila for many years as a fitness trainer and workout class instructor.</span>
      <span class="line">She is truly one of the very best in the business. Mila is extremely knowledgeable about human</span>
      <span class="line">physiology and teaching. Her personality is professional, informative, and caring. She would</span>
      <span class="line">always put &ldquo;her all&rdquo; into each of her classes.</span>
    </p>
    <span class="outline-button quote-author">Harriet Sommers</span>
    <span class="quote-mark quote-close">&rdquo;</span>
  </section>

  <section class="content-band group-band">
    <h2 class="section-heading">Group Classes/ Boot Camps</h2>
    <p class="section-copy">
      <span class="line">Quelborn Group Exercise classes are designed for people</span>
      <span class="line">of all fitness levels. Quelborn's group classes take a holistic</span>
      <span class="line">approach and make sure you work out in a balanced</span>
      <span class="line">way that feeds your body and spirit. Classes are taught</span>
      <span class="line">with a variety of approaches including pilates, yoga,</span>
      <span class="line">suspension, dance, and much more to keep things fresh and</span>
      <span class="line">challenging.</span>
    </p>
    <span class="solid-button">READ MORE</span>
    <div class="inset-photo group-photo" role="img" aria-label="Trainer in a pink top doing a side stretch on a lawn"></div>
  </section>

  <div class="photo stretch-photo" role="img" aria-label="Trainer reaching one arm overhead in a green park"></div>

  <section class="content-band training-band">
    <div class="inset-photo training-photo" role="img" aria-label="Trainer in a blue top holding a deep stretch against a tree"></div>
    <h2 class="section-heading">Personal Training</h2>
    <p class="section-copy">
      <span class="line">Private sessions will provide you with the motivation you</span>
      <span class="line">need to reach your goals. As an FTA certified trainer,</span>
      <span class="line">Mila will make sure you're working out safely and keep</span>
      <span class="line">the workouts fresh and exciting so you can achieve your</span>
      <span class="line">goals.</span>
    </p>
    <span class="outline-button training-more">Read More</span>
  </section>

  <div class="photo group-stretch-photo" role="img" aria-label="Smiling group stretching with arms raised among park trees"></div>

  <section class="subscribe">
    <h2 class="subscribe-title">Subscribe</h2>
    <p class="subscribe-note">Sign up with your email address to receive the latest news and updates.</p>
    <span class="field" style="left:248px">First Name</span>
    <span class="field" style="left:495px">Last Name</span>
    <span class="field" style="left:742px">Email Address</span>
    <span class="signup-button">SIGN UP</span>
    <p class="privacy-note">We respect your privacy.</p>
  </section>

  <footer class="contact-footer">
    <div class="contact-intro">
      <h2 class="footer-heading">Got a question or comment?</h2>
      <p>
        <span class="line">We are constantly working to raise the</span>
        <span class="line">bar on our services. If you have any</span>
        <span class="line">questions or concerns about your</span>
        <span class="line">experience, please let us know.</span>
      </p>
    </div>
    <svg class="contact-notch" width="14" height="24" viewBox="0 0 14 24"><path d="M0 0 L12 12 L0 24 Z" fill="#000"/></svg>
    <div class="trainer-card">
      <h2 class="footer-heading">Mila Orlova</h2>
      <div class="contact-line" style="top:80px">
        <svg viewBox="0 0 18 14"><path d="M1 4 Q9 -1 17 4 L15 7 L12 5.5 L12 3.5 Q9 2.5 6 3.5 L6 5.5 L3 7 Z M4 8 H14 L16 13 H2 Z" fill="#fff"/></svg>
        <span>+1 (555) 014-2380</span>
      </div>
      <div class="contact-line" style="top:107px">
        <svg viewBox="0 0 18 14"><rect x="1" y="1" width="16" height="12" fill="#fff"/><path d="M1 1 L9 8 L17 1" fill="none" stroke="#1b1b1b" stroke-width="1.5"/></svg>
        <span>orlova@mailbox.net</span>
      </div>
    </div>
  </footer>

  <div class="bottom-bar">
    <span class="follow-label">FOLLOW US</span>
    <div class="social-list">
      <span class="social-square"></span>
      <span class="social-square"></span>
      <span class="social-square"></span>
      <span class="social-square"></span>
      <span class="social-square"></span>
      <span class="social-square"></span>
    </div>
    <span class="copyright">Copyright &copy; 2024. All Rights Reserved. Quelborn Fitness Lodi, California.</span>
  </div>

</div>
</body>
</html>
```